Web Design job - Condo Debts Collection Business needs a Web Design

I need a site for a client, who works with condo debts collection, and ensure all revenues provided by condo fees will be always available to the building manager of condo on a specific date, regardless of defaults.
I have the visual identity (logo, slogan and colors) of the company, and some requirements on layout (kind of slider, menu options, phone number on a noble position, etc) - maybe I can do a sketch, but I like the idea of give some freedom to designer.

*** PLEASE, we have no interest in templates. We want something new***

Target Market(s)

I have two targets for this design: - Condominium's building manager. This target is looking for a solution to overdue debts on it's condo. - Residents on condominiums. This target wants to live in a better place, where their neighbors pay their condominium fees on time.

Number of Pages Required

1 page

Requirements
Must have
• - Slider with title, some short text related, a nice image (I prefer happy and/or peaceful family, people doing business, happy friends, and so on).
• - I have a special attention to menu. I'm looking for one I can have a nice effect, more elegant, charming, kind of innovative.
• - Phone number on the top (or clearly visible).
• - Member log in area or icon on the top (or clearly visible).
• - News/articles area.
• - Modern fonts, with good quality, sans-serif on areas where reading is more intensive (prefer Google web-fonts).
• - Colors specified on attached files.
Nice to have
• - Clear background color, cause it's better to read larger texts (like articles). Dark backgrounds makes reading difficult.
• - A site with effects (like shadows, lines, curves, gradients, lights) is usually pretty.
• - I pay attention on beautiful footers.
Should not have
• - Images with a lot of money (I don't sell richness, I sell tranquility, peace, harmony, safety).
• - Poor menu.

```html
<!DOCTYPE html>
<html lang="en">
<head>
<meta charset="utf-8">
<title>Valdora – Condo Fee Assurance</title>
<link href="https://fonts.googleapis.com/css2?family=Playfair+Display:wght@700&family=Lato:wght@400;700&display=swap" rel="stylesheet">
<style>
:root{
  --gold:#e1a11f;
  --gold-dark:#c98c12;
  --ink:#1a1a1a;
  --dark:#141414;
  --text:#7d7d7d;
  --grey-bg:#efeeef;
  --white:#ffffff;
  --line:#e2e2e2;
}
*{box-sizing:border-box;margin:0;padding:0}
html,body{width:1200px;height:4167px;overflow:hidden}
body{position:relative;background:var(--white);font-family:'Lato',Arial,sans-serif;color:var(--text)}
.abs{position:absolute}
.serif{font-family:'Playfair Display',Georgia,serif}

/* hero */
.hero{left:0;top:0;width:1200px;height:765px;background:linear-gradient(180deg,#0d0d0d,#241b12 60%,#1a140e);overflow:hidden}
.hero-photo{left:230px;top:0;width:740px;height:765px;background:radial-gradient(ellipse at 50% 55%,#b07a4a 0%,#7a4e2c 35%,#3a2616 70%,rgba(20,15,10,0) 100%);clip-path:polygon(50% 0,100% 25%,100% 100%,0 100%,0 25%)}
.brand{font-family:'Lato',Arial,sans-serif;font-weight:700;color:var(--white);font-size:44px;letter-spacing:1px;display:flex;align-items:center;gap:12px}
.brand .mark{width:26px;height:26px;background:var(--gold)}
.topbar-phone{left:626px;top:74px;color:var(--white);font-weight:700;font-size:24px;display:flex;align-items:center;gap:12px}
.member{left:925px;top:68px;width:175px;height:46px;border-radius:23px;background:var(--gold);color:var(--white);font-weight:700;font-size:17px;display:flex;align-items:center;gap:10px;padding-left:6px}
.member .ico{width:36px;height:36px;border-radius:50%;background:var(--white);display:flex;align-items:center;justify-content:center}
.hero-title{left:0;width:1200px;top:410px;text-align:center;color:var(--white);font-size:92px;letter-spacing:2px}
.hero-sub{left:0;width:1200px;top:532px;text-align:center;color:#f1e6da;font-size:20px}
.btn{display:flex;align-items:center;justify-content:center;border-radius:26px;font-weight:700;font-size:15px;color:var(--white);text-transform:uppercase}
.btn-gold{background:var(--gold)}
.btn-ghost{border:2px solid var(--white)}
.arrow{width:46px;height:46px;border:2px solid var(--white);border-radius:50%;display:flex;align-items:center;justify-content:center}

/* menu */
.menu{left:97px;top:728px;width:1006px;height:72px}
.menu ul{position:absolute;left:0;top:0;width:100%;height:72px;list-style:none;display:flex;align-items:center}
.menu li{position:absolute;color:var(--white);font-weight:700;font-size:18px}
.search{left:692px;top:18px;width:231px;height:36px;border-radius:18px;background:var(--white);color:#999;font-size:14px;padding:9px 18px}

/* headings */
.section-title{color:var(--ink);font-size:44px}
.divider{width:64px;height:14px}

.body-copy{font-size:14.5px;line-height:32px;color:var(--text)}

/* news */
.grey{left:0;top:1542px;width:1200px;height:980px;background:var(--grey-bg);clip-path:polygon(0 83px,1200px 0,1200px 980px,0 980px)}
.card{background:var(--white);box-shadow:0 2px 8px rgba(0,0,0,.12)}
.photo{position:absolute}
.card h3{font-family:'Lato',Arial,sans-serif;color:var(--ink);font-size:20px;font-weight:700;line-height:28px}
.date{color:var(--gold);font-size:13px;display:flex;align-items:center;gap:8px}
.card p{font-size:13.5px;line-height:24px;color:var(--text)}

/* contact */
.contact{left:0;top:3080px;width:1200px;height:637px;background:var(--dark);clip-path:polygon(0 70px,1200px 0,1200px 637px,0 637px)}
.map{left:330px;top:3260px;width:500px;height:300px;background:radial-gradient(ellipse,#3a3a3a 0%,rgba(20,20,20,0) 70%);opacity:.7}
.form-card{left:669px;top:3081px;width:434px;height:525px;background:var(--white);box-shadow:0 4px 18px rgba(0,0,0,.25)}
.field{position:absolute;left:39px;width:353px;height:44px;border:1px solid var(--line);font-size:13px;color:#999;display:flex;align-items:center;gap:10px;padding-left:14px}
.submit{position:absolute;left:39px;top:428px;width:353px;height:44px;background:var(--gold);color:var(--white);font-weight:700;font-size:14px;display:flex;align-items:center;justify-content:center;text-transform:uppercase}
.icon-circle{width:50px;height:50px;border:2px solid var(--white);border-radius:50%;display:flex;align-items:center;justify-content:center}

/* footer */
.footer-nav{left:0;width:1200px;top:3950px;display:flex;justify-content:center;gap:50px;color:var(--ink);font-size:18px}
.socials{left:0;width:1200px;top:4015px;display:flex;justify-content:center;gap:16px}
.socials span{width:32px;height:32px;border:2px solid var(--gold);border-radius:50%;display:flex;align-items:center;justify-content:center}
.socials span i{width:8px;height:8px;background:var(--gold);border-radius:50%}
.copyright{left:0;width:1200px;top:4076px;text-align:center;font-size:14px;color:#555}
.bottom-line{left:0;top:4157px;width:1200px;height:10px;background:var(--gold)}
</style>
</head>
<body>

<!-- Hero slider -->
<section class="abs hero">
  <div class="abs hero-photo" role="img" aria-label="Slider image: happy friends and families in warm sunlight arranged in a triangular mosaic"></div>
  <div class="abs brand" style="left:100px;top:60px"><span class="mark"></span>Valdora</div>
  <div class="abs topbar-phone">
    <svg width="22" height="22" viewBox="0 0 24 24"><path fill="#e1a11f" d="M6.6 10.8a15 15 0 0 0 6.6 6.6l2.2-2.2c.3-.3.7-.4 1-.2 1.1.4 2.3.6 3.6.6.6 0 1 .4 1 1V20c0 .6-.4 1-1 1A17 17 0 0 1 3 4c0-.6.4-1 1-1h3.5c.6 0 1 .4 1 1 0 1.3.2 2.5.6 3.6.1.3 0 .7-.2 1z"/></svg>
    Phone : 1 888 888 8888
  </div>
  <div class="abs member"><span class="ico"><svg width="20" height="20" viewBox="0 0 24 24"><circle cx="12" cy="8" r="4" fill="#e1a11f"/><path d="M4 21c0-4.4 3.6-7 8-7s8 2.6 8 7z" fill="#e1a11f"/></svg></span>Member Login</div>
  <div class="abs arrow" style="left:47px;top:394px"><svg width="14" height="14" viewBox="0 0 14 14"><path d="M9 2 4 7l5 5" stroke="#fff" stroke-width="2" fill="none"/></svg></div>
  <div class="abs arrow" style="left:1105px;top:394px"><svg width="14" height="14" viewBox="0 0 14 14"><path d="M5 2l5 5-5 5" stroke="#fff" stroke-width="2" fill="none"/></svg></div>
  <h1 class="abs hero-title serif">VALDORA</h1>
  <p class="abs hero-sub">Sed ut perspiciatis unde omnis iste natus error svoluptatem accusantium</p>
  <div class="abs btn btn-gold" style="left:438px;top:590px;width:140px;height:50px">Read more</div>
  <div class="abs btn btn-ghost" style="left:586px;top:590px;width:178px;height:50px">News &amp; Events</div>
</section>

<!-- Menu -->
<nav class="abs menu">
  <svg class="abs" width="1006" height="120" viewBox="0 0 1006 120" style="left:0;top:0">
    <defs><radialGradient id="menuShadow" cx="50%" cy="0%" r="50%"><stop offset="0" stop-color="#000" stop-opacity=".28"/><stop offset="1" stop-color="#000" stop-opacity="0"/></radialGradient></defs>
    <ellipse cx="503" cy="72" rx="320" ry="34" fill="url(#menuShadow)"/>
    <polygon points="36,0 970,0 1006,36 970,72 36,72 0,36" fill="#e1a11f"/>
  </svg>
  <ul>
    <li style="left:82px">Home</li>
    <li style="left:178px">About us</li>
    <li style="left:296px">Services</li>
    <li style="left:410px">News &amp; Events</li>
    <li style="left:572px">Contact us</li>
  </ul>
  <div class="abs search">Search...</div>
</nav>

<!-- About -->
<section>
  <h2 class="abs section-title serif" style="left:100px;top:956px">About us</h2>
  <svg class="abs divider" style="left:100px;top:1032px" viewBox="0 0 64 14"><line x1="0" y1="7" x2="22" y2="7" stroke="#ccc"/><line x1="42" y1="7" x2="64" y2="7" stroke="#ccc"/><rect x="27" y="2" width="10" height="10" fill="#e1a11f"/></svg>
  <p class="abs body-copy" style="left:100px;top:1068px;width:450px">Sed ut perspiciatis unde omnis iste natus error sit voluptatem accusantium doloremque laudantium, totam rem aperiam, eaque ipsa quae ab illo inventore veritatis et quasi architecto beatae vitae dicta sunt explicabo. Nemo enim ipsam voluptatem quia voluptas sit aspernatur aut odit aut fugit, sed quia consequuntur magni doloribus eos qui ratione sequi nesciunt. Nemo enim ipsam voluptatem quia voluptas sit aspernatur aut odit aut fugit, sed quia consequuntur magni dolores eos qui rationem...</p>
  <div class="abs btn btn-gold" style="left:100px;top:1328px;width:139px;height:50px">Read more</div>
  <div class="abs" style="left:597px;top:964px;width:506px;height:392px;border:3px solid var(--gold)"></div>
  <div class="abs photo" style="left:617px;top:981px;width:486px;height:400px;background:linear-gradient(135deg,#d9dde0,#8a9199 55%,#4a5058)" role="img" aria-label="Business team meeting around a table in a bright office"></div>
</section>

<!-- News & Events -->
<div class="abs grey"></div>
<section>
  <h2 class="abs section-title serif" style="left:0;width:1200px;text-align:center;top:1718px">News &amp; Events</h2>
  <svg class="abs divider" style="left:568px;top:1790px" viewBox="0 0 64 14"><line x1="0" y1="7" x2="22" y2="7" stroke="#ccc"/><line x1="42" y1="7" x2="64" y2="7" stroke="#ccc"/><rect x="27" y="2" width="10" height="10" fill="#e1a11f"/></svg>

  <article class="abs card" style="left:100px;top:1872px;width:450px;height:434px">
    <div class="photo" style="left:6px;top:6px;width:438px;height:283px;background:linear-gradient(160deg,#c8cacc,#6d7277 60%,#3e4246)" role="img" aria-label="Two businessmen walking outside an office building"></div>
    <h3 class="abs" style="left:30px;top:314px">Quia non numqua nostrum accusantium</h3>
    <div class="abs date" style="left:30px;top:352px"><svg width="13" height="13" viewBox="0 0 14 14"><rect x="1" y="2" width="12" height="11" fill="#e1a11f"/></svg>July 10,2018</div>
    <p class="abs" style="left:30px;top:382px">Sed ut perspiciatis unde omnis iste natus error sit voluptate...</p>
  </article>

  <article class="abs card" style="left:572px;top:1872px;width:531px;height:206px">
    <div class="photo" style="left:6px;top:6px;width:175px;height:194px;background:linear-gradient(150deg,#d8d6d2,#8c8a86 60%,#4d4b48)" role="img" aria-label="Business handshake over a desk"></div>
    <h3 class="abs" style="left:211px;top:30px;width:300px">Quia noaccusantiumumqua nostrum accu santium</h3>
    <div class="abs date" style="left:211px;top:98px"><svg width="13" height="13" viewBox="0 0 14 14"><rect x="1" y="2" width="12" height="11" fill="#e1a11f"/></svg>July 10,2018</div>
    <p class="abs" style="left:211px;top:126px;width:300px">Sed ut perspiciatis unaccusantium de omnis iste natuaccusantium error...</p>
  </article>

  <article class="abs card" style="left:572px;top:2100px;width:531px;height:206px">
    <div class="photo" style="left:6px;top:6px;width:175px;height:194px;background:linear-gradient(150deg,#b9b3ab,#6b635a 60%,#3a342e)" role="img" aria-label="Hands reviewing documents on a desk"></div>
    <h3 class="abs" style="left:211px;top:30px;width:300px">Quia noaccusantiumumqua nostrum accu santium</h3>
    <div class="abs date" style="left:211px;top:98px"><svg width="13" height="13" viewBox="0 0 14 14"><rect x="1" y="2" width="12" height="11" fill="#e1a11f"/></svg>July 10,2018</div>
    <p class="abs" style="left:211px;top:126px;width:300px">Sed ut perspiciatis unaccusantium de omnis iste natuaccusantium error...</p>
  </article>

  <div class="abs btn btn-gold" style="left:508px;top:2364px;width:184px;height:50px;text-transform:none;font-size:17px">View All News</div>
</section>

<!-- Testimonials -->
<section>
  <h2 class="abs section-title serif" style="left:0;width:1200px;text-align:center;top:2658px">Client Testimonials</h2>
  <svg class="abs divider" style="left:568px;top:2735px" viewBox="0 0 64 14"><line x1="0" y1="7" x2="22" y2="7" stroke="#ccc"/><line x1="42" y1="7" x2="64" y2="7" stroke="#ccc"/><rect x="27" y="2" width="10" height="10" fill="#e1a11f"/></svg>
  <p class="abs body-copy" style="left:228px;top:2788px;width:744px;text-align:center;font-style:italic">Sed ut perspiciatis unde omnis iste natus error sit voluptatem accusantium doloremque laudantium, totam rem aperiam, eaque ipsa quae ab illo inventore veritatis et quasi architecto beatae vitae dicta sunt explicabo nemo ipsam voluptatem quia voluptas sit aspernatur aut odit aut fugitsd quia consequuntur magni dolori ratione voluptatem sequi nesciunt.</p>
  <div class="abs" style="left:0;width:1200px;top:2898px;display:flex;justify-content:center;align-items:center;gap:10px;color:var(--ink);font-weight:700;font-size:16px">- Quis nostrum
    <svg width="84" height="16" viewBox="0 0 84 16"><g fill="#e1a11f"><path id="st" d="M8 0l2.4 5 5.6.6-4.2 3.8 1.2 5.6L8 12.2 3 15l1.2-5.6L0 5.6 5.6 5z"/><use href="#st" x="17"/><use href="#st" x="34"/><use href="#st" x="51"/><use href="#st" x="68"/></g></svg>
  </div>
  <svg class="abs" style="left:578px;top:2948px" width="44" height="20" viewBox="0 0 44 20"><path d="M14 3 7 10l7 7" stroke="#e1a11f" stroke-width="2.5" fill="none"/><path d="M30 3l7 7-7 7" stroke="#1a1a1a" stroke-width="2.5" fill="none"/></svg>
</section>

<!-- Contact -->
<div class="abs contact"></div>
<div class="abs map" role="img" aria-label="Faint dotted world map"></div>
<section>
  <h2 class="abs serif" style="left:100px;top:3300px;color:var(--white);font-size:40px">Contact us</h2>
  <div class="abs" style="left:100px;top:3360px;width:40px;height:3px;background:var(--gold)"></div>
  <p class="abs" style="left:100px;top:3392px;width:460px;color:#e6e6e6;font-size:14px;line-height:30px">Sed ut perspiciatis unde omnis iste natus error sit voluptatem totam rem aperiaque ipsa quae ab illo inventore..</p>
  <div class="abs icon-circle" style="left:100px;top:3484px"><svg width="18" height="22" viewBox="0 0 18 22"><path d="M9 0a8 8 0 0 0-8 8c0 6 8 14 8 14s8-8 8-14a8 8 0 0 0-8-8zm0 11a3 3 0 1 1 0-6 3 3 0 0 1 0 6z" fill="#fff"/></svg></div>
  <p class="abs" style="left:164px;top:3486px;width:300px;color:#e6e6e6;font-size:14px;line-height:24px">124,Nemo enim ipsam voluptatemed quia non numqed quumquamsam..</p>
  <div class="abs icon-circle" style="left:100px;top:3556px"><svg width="20" height="20" viewBox="0 0 24 24"><path fill="#fff" d="M6.6 10.8a15 15 0 0 0 6.6 6.6l2.2-2.2c.3-.3.7-.4 1-.2 1.1.4 2.3.6 3.6.6.6 0 1 .4 1 1V20c0 .6-.4 1-1 1A17 17 0 0 1 3 4c0-.6.4-1 1-1h3.5c.6 0 1 .4 1 1 0 1.3.2 2.5.6 3.6.1.3 0 .7-.2 1z"/></svg></div>
  <p class="abs" style="left:164px;top:3572px;color:#e6e6e6;font-size:14px">Phone : 1 888 888 8888</p>

  <form class="abs form-card">
    <h3 class="abs serif" style="left:0;width:434px;text-align:center;top:44px;color:var(--ink);font-size:32px">Say Hello To Valdora</h3>
    <div class="abs" style="left:197px;top:100px;width:40px;height:3px;background:var(--gold)"></div>
    <div class="field" style="top:147px"><svg width="12" height="12" viewBox="0 0 12 12"><circle cx="6" cy="4" r="3" fill="#999"/><path d="M0 12c0-3 3-5 6-5s6 2 6 5z" fill="#999"/></svg>Enter Name</div>
    <div class="field" style="top:211px"><svg width="13" height="10" viewBox="0 0 13 10"><rect x=".5" y=".5" width="12" height="9" fill="none" stroke="#999"/><path d="M.5.5l6 5 6-5" fill="none" stroke="#999"/></svg>Enter Email</div>
    <div class="field" style="top:269px"><svg width="12" height="12" viewBox="0 0 12 12"><path d="M1 11l1-3 7-7 2 2-7 7z" fill="#999"/></svg>Subject</div>
    <div class="field" style="top:330px;height:83px;align-items:flex-start;padding-top:14px"><svg width="12" height="12" viewBox="0 0 12 12"><rect x=".5" y=".5" width="11" height="11" fill="none" stroke="#999"/></svg>Message</div>
    <div class="submit">Submit Message</div>
  </form>
</section>

<!-- Footer -->
<footer>
  <div class="abs brand" style="left:0;width:1200px;top:3826px;justify-content:center;color:var(--ink);font-size:56px"><span class="mark" style="width:34px;height:34px"></span>Valdora</div>
  <nav class="abs footer-nav"><span>Home</span><span>About us</span><span>Services</span><span>News &amp; Events</span><span>Contact us</span></nav>
  <div class="abs socials"><span><i></i></span><span><i></i></span><span><i></i></span><span><i></i></span><span><i></i></span><span><i></i></span><span><i></i></span></div>
  <p class="abs copyright">Copyright © Valdora 2018.All Rights Reserved</p>
  <div class="abs bottom-line"></div>
</footer>

</body>
</html>
```